regPersonal Trainer Flyer Design

Project Deadline Extended
Reason: I have been very busy with other work and would like to extend the deadline to offer designers the chance to edit and improve designs with my help. Thank you for all the designs that have been sent so far.

```html
<!DOCTYPE html>
<html lang="en">
<head>
<meta charset="utf-8">
<title>Personal Trainer Flyer – Sam Redford</title>
<link rel="stylesheet" href="https://fonts.googleapis.com/css2?family=Open+Sans:wght@300;400;600;700;800&family=Kaushan+Script&display=swap">
<style>
  :root {
    --red: #ee2a1b;
    --charcoal: #3b3d3b;
    --blue: #1d6ff0;
    --white: #ffffff;
    --ink: #141414;
    --photo-warm: #b9a79c;
    --photo-cool: #9aa0a6;
    --photo-light: #d8d4cf;
  }
  * { margin: 0; padding: 0; box-sizing: border-box; }
  html, body { width: 1200px; height: 851px; overflow: hidden; background: var(--white); }
  .flyer {
    position: relative;
    width: 1200px;
    height: 851px;
    overflow: hidden;
    background: var(--white);
    font-family: "Open Sans", Arial, sans-serif;
  }
  .backdrop { position: absolute; inset: 0; }
  .headline { position: absolute; left: 55px; top: 414px; color: var(--white); }
  .headline-main {
    font-size: 96px; font-weight: 800; line-height: 1; letter-spacing: -1px;
    transform: scaleX(0.92); transform-origin: left;
    text-shadow: 2px 2px 3px rgba(0,0,0,0.25);
  }
  .headline-sub {
    margin-top: 18px; font-size: 46px; font-weight: 800; color: var(--ink);
    letter-spacing: 14px; line-height: 1;
  }
  .headline-tag {
    margin-top: 20px; font-size: 34px; font-weight: 300; letter-spacing: -0.5px; line-height: 1;
    transform: scaleX(0.92); transform-origin: left;
  }
  .pitch-list {
    position: absolute; left: 465px; top: 424px; list-style: none;
    color: var(--white); font-size: 25px; font-weight: 600; line-height: 29.5px;
  }
  .pitch-list li { position: relative; padding-left: 30px; }
  .pitch-list li::before {
    content: ""; position: absolute; left: 0; top: 9px;
    border-left: 11px solid var(--ink);
    border-top: 6px solid transparent; border-bottom: 6px solid transparent;
  }
  .offer {
    position: absolute; left: 950px; top: 510px; width: 190px;
    color: var(--white); font-family: "Kaushan Script", cursive;
    text-align: center; line-height: 1; transform: rotate(16deg);
  }
  .offer-small { font-size: 27px; display: block; }
  .offer-big { font-size: 62px; display: block; margin: 2px 0; }
  .role {
    position: absolute; left: 92px; top: 752px;
    color: var(--white); font-size: 30px; font-weight: 400; letter-spacing: -0.5px;
  }
  .trainer-name {
    position: absolute; left: 412px; top: 733px;
    color: var(--white); font-family: "Kaushan Script", cursive; font-size: 62px; line-height: 1;
  }
  .contact {
    position: absolute; left: 830px; top: 740px;
    color: var(--white); font-size: 25px; font-weight: 700; line-height: 32px;
  }
</style>
</head>
<body>
<main class="flyer">
  <svg class="backdrop" width="1200" height="851" viewBox="0 0 1200 851" aria-hidden="false">
    <defs>
      <linearGradient id="gym-warm" x1="0" y1="0" x2="1" y2="1">
        <stop offset="0" stop-color="#cfc6bd"/>
        <stop offset="1" stop-color="#8f8580"/>
      </linearGradient>
      <linearGradient id="gym-cool" x1="0" y1="0" x2="1" y2="1">
        <stop offset="0" stop-color="#e0dcd6"/>
        <stop offset="1" stop-color="#a7a8ab"/>
      </linearGradient>
      <linearGradient id="gym-mid" x1="0" y1="0" x2="1" y2="0">
        <stop offset="0" stop-color="#bda79d"/>
        <stop offset="1" stop-color="#8d9297"/>
      </linearGradient>
    </defs>

    <!-- red panel -->
    <polygon class="panel-red" fill="var(--red)" points="0,0 1200,0 1200,520 1040,470 800,684 0,684"/>

    <!-- photography areas -->
    <polygon class="photo photo-workout-pair" role="img" aria-label="Photo: trainer and client working with suspension straps and boxing pads"
      fill="url(#gym-warm)" stroke="var(--white)" stroke-width="6"
      points="0,-5 600,-5 470,190 330,300 0,235"/>
    <polygon class="photo photo-squat-coaching" role="img" aria-label="Photo: trainer coaching a client through a squat in the gym"
      fill="url(#gym-cool)" stroke="var(--white)" stroke-width="6"
      points="625,-5 1205,-5 1205,330 500,205"/>
    <polygon class="photo photo-floor-exercises" role="img" aria-label="Photo: clients lifting a barbell and doing sit-ups with the trainer"
      fill="url(#gym-mid)" stroke="var(--white)" stroke-width="6"
      points="480,225 1205,350 1205,510 1040,462 410,330"/>

    <!-- offer panel -->
    <polygon class="panel-offer" fill="var(--charcoal)" stroke="var(--white)" stroke-width="6"
      points="805,690 1042,470 1205,518 1205,690"/>

    <!-- footer band -->
    <rect x="0" y="684" width="1200" height="16" fill="var(--white)"/>
    <polygon class="footer-role" fill="var(--charcoal)" points="0,700 330,700 375,775 330,851 0,851"/>
    <polygon class="footer-contact" fill="var(--blue)" points="352,700 1200,700 1200,851 352,851 397,775"/>
  </svg>

  <div class="headline">
    <div class="headline-main">FITNESS</div>
    <div class="headline-sub">TRAINING</div>
    <div class="headline-tag">IMPROVE YOUR HEALTH</div>
  </div>

  <ul class="pitch-list">
    <li>Lacking motivation?</li>
    <li>Not achieving your goals?</li>
    <li>Need help?</li>
    <li>Bored of the gym?</li>
    <li>You're never too old</li>
    <li>I can help improve your<br>health and well-being</li>
  </ul>

  <div class="offer">
    <span class="offer-small">One</span>
    <span class="offer-big">FREE</span>
    <span class="offer-small">Session</span>
  </div>

  <div class="role">Personal Trainer</div>
  <div class="trainer-name">Sam Redford</div>
  <div class="contact">
    <div>07700900418</div>
    <div>samredford@mailbox.co.uk</div>
  </div>
</main>
</body>
</html>
```